KVT Web Design Project

I would like a simple and elegant design for my international business consulting practice web site. I already have new KVT Logo and will have brochure-colors are blue, green and black

Practice areas:
I offer consulting services specializing in developing Internet-based anti-counterfeiting and anti-fraud programs, test purchases and investigations.

I offer Cyber Security, Data Protection and Compliance services

I also offer International Due Diligence Investigations and Country and Travel Risk Assessments

General Background Investigations

Physical Security Services

About me section listing my Bio

I have a set of key associates that I work with around the world and will want to list their CVs or Bios under "KVT

Associates"Banner with nice photo but not too cluttered

Ability to Upload documents and articles

Contact us section
Updates

I have uploaded my new logo-please advise if you didn't get it or it is not in the correct file format.

Thank you

Dominic

Hello Everyone,

Thank you for your submissions and ideas. I'm not sure about design only vs code. I understand that some of you do not do code-if not then please just provide design.

More about my business: see below link on Google docs to my brochure-this should help but don't use that phone number-see below.

https://files.quillbin.example/view?id=7Qx2Lm9Pz4Rt8Kw3Hn6Vb1Jc5Fd0Sg

 

Here are some details.

Contacts:

Dominic R. Torvello, CPP

President

Torvello and Associates, LLC

P.O. Box 47129

Gaithersburg, MD 20914

USA

web address:www.Torvelloandassociates.example (currently not working)

email:dom @torvelloand associates.example

Tel: 202-555-0173

I hope this is helpful. Dom

Reason: Sorry but during holiday period, have not had as much time to devote to this project. Thanks for your submissions.

Per my previous guidance, please keep designs simple and elegant and free from traditional security images with locks and chains-I prefer one or at most, two photos. Two colors- blue and green in addition to black for print. I want to present professional, corporate and international image. Thank you for your ideas nad submissions.

Dom

Target Market(s)

Law firms, large multi-national corporations, Security Industry

Industry/Entity Type

Business

Requirements
Must have
• Must have sections: (will provide text)

About KVT (will provide text)

Practice areas

Associates (will provide text)

Contact us

(it must also have ability to upload files and articles)
Should not have
• Old style fonts and symbols such as security badges, scales of justice, etc. I want a sleek and modern design.

```html
<!DOCTYPE html>
<html lang="en">
<head>
<meta charset="utf-8">
<title>Torvello &amp; Associates, LLC</title>
<link rel="stylesheet" href="https://fonts.googleapis.com/css2?family=Arimo:wght@400;700&family=Michroma&display=swap">
<style>
:root{
  --sky:#c9eef8;
  --sky-deep:#8fd9ee;
  --teal:#0f9a9c;
  --teal-dark:#0a6f72;
  --teal-deep:#066266;
  --cyan:#1cc4f0;
  --cyan-light:#5fd7f7;
  --ink:#333;
  --ink-soft:#444;
  --brand-blue:#1a5fa0;
  --date-red:#b0162a;
  --panel-line:#cfd6d8;
}
*{box-sizing:border-box;margin:0;padding:0}
html,body{width:1081px;height:1200px;overflow:hidden}
body{
  position:relative;
  font-family:"Arimo",Arial,sans-serif;
  color:var(--ink);
  background:
    radial-gradient(circle at 80% 5%, #e6f8fd 0, transparent 40%),
    linear-gradient(180deg,#d6f3fb 0,#bfe9f5 60%,var(--teal) 94%,var(--teal) 100%);
}
.abs{position:absolute}

/* header */
.brand{left:29px;top:36px;display:flex;flex-direction:column;gap:4px}
.brand-row{display:flex;align-items:center;gap:10px}
.brand-mark{font-size:26px;color:var(--brand-blue);padding-right:10px;border-right:1px solid var(--brand-blue);line-height:32px}
.brand-name{font-size:24px;color:#1f3550;line-height:32px}
.brand-tag{font-size:14.5px;letter-spacing:2.6px;color:var(--brand-blue)}

.nav{left:467px;top:38px;width:588px;height:50px;border-radius:3px;
  background:linear-gradient(180deg,#1fb1b3,var(--teal) 50%,#0b8587);
  border:1px solid #0b7f82;display:flex;align-items:center;box-shadow:0 2px 4px rgba(0,0,0,.2)}
.nav a{flex:auto;text-align:center;color:#fff;font-size:13.5px;text-decoration:none;border-right:1px solid rgba(255,255,255,.55);line-height:26px}
.nav a:last-child{border-right:0}

/* slider */
.slider{left:21px;top:112px;width:1037px;height:373px;border-radius:10px;border:1px solid #c9d2d5;
  background:linear-gradient(180deg,#fdfdfd,#f0f2f3)}
.slide-stage{left:15px;top:10px;width:1007px;height:351px;border-radius:8px;
  background:radial-gradient(ellipse at 60% 30%,#ffffff 0,#eef1f2 60%,#e3e7e9 100%)}
.slide-photo{left:60px;top:40px;width:380px;height:305px;border-radius:6px;
  background:radial-gradient(ellipse at 50% 50%,#c3c8cc 0,#dfe3e5 60%,transparent 75%)}
.slide-title{left:494px;top:251px;font-family:"Michroma",sans-serif;font-size:31px;letter-spacing:1px;color:#1b1b1b}
.slide-copy{left:497px;top:292px;width:500px;font-size:13px;line-height:22.7px;color:#444}
.btn-grey{left:875px;top:399px;width:90px;height:32px;background:#9a9a9a;color:#fff;font-size:12.5px;display:flex;align-items:center;justify-content:center}
.arrow{top:279px;width:39px;height:39px;border-radius:50%;background:#f4f4f4;border:1px solid #b8bec1;display:flex;align-items:center;justify-content:center}
.arrow.prev{left:21px}.arrow.next{left:1020px}

/* content panel */
.content{left:21px;top:497px;width:1038px;height:633px;
  background:linear-gradient(180deg,#ffffff 0,#eef7f8 45%,#d4ecef 100%);
  border:1px solid #d3dadc;box-shadow:0 0 10px rgba(0,0,0,.15)}
.card{top:509px;width:253px;height:319px;background:linear-gradient(180deg,#129ea0,var(--teal) 50%,#0c8a8c);border-top:11px solid var(--teal-dark)}
.card-head{height:48px;background:linear-gradient(180deg,var(--cyan-light),var(--cyan));display:flex;align-items:center;justify-content:center;text-align:center;color:#1d2b33;font-weight:700;font-size:15.5px;line-height:22px}
.card p{margin:34px 12px 0 15px;color:#fff;font-size:13px;line-height:19.5px}
.card .btn{position:absolute;right:6px;bottom:6px;width:90px;height:37px;background:var(--cyan);color:#fff;font-size:13px;display:flex;align-items:center;justify-content:center}

h2{font-weight:400;font-size:27px;color:#222}
.welcome{left:41px;top:853px;width:440px}
.welcome p{font-size:12.5px;line-height:21.5px;color:#333}
.welcome .lead{margin-top:11px}
.person{left:39px;top:977px;width:127px;height:121px;background:var(--teal);padding:6px}
.person div{width:100%;height:100%;background:linear-gradient(160deg,#f4f6f8,#cfd9e0)}
.welcome-strong{left:179px;top:976px;width:310px;font-weight:700;font-size:12.5px;line-height:21.5px;color:#222}
.welcome-more{left:179px;top:1039px;width:310px;font-size:12.5px;line-height:21.5px;color:#333}

.divider{top:867px;width:1px;height:240px;background:var(--panel-line)}
.projects{left:506px;top:853px;width:300px}
.project{display:flex;gap:10px;margin-top:12px}
.project:first-of-type{margin-top:18px}
.thumb{flex:none;width:68px;height:65px;border:3px solid #c9d0d3;background:linear-gradient(135deg,#6fa8c7,#2c5f80)}
.project p{font-size:12.5px;line-height:19.5px;color:#333;margin-top:-2px}

.news{left:814px;top:853px;width:230px}
.news-item{border-bottom:1px solid var(--panel-line);padding:0 6px 6px;margin-top:10px}
.news-item:last-child{border-bottom:0}
.news-date{font-size:11.5px;color:var(--date-red);margin-bottom:8px}
.news-item p{font-size:12.5px;line-height:19.5px;color:#333}
.news-item a{color:var(--date-red);text-decoration:none}

/* footer */
.footer{left:21px;top:1130px;width:1038px;height:70px;background:var(--teal-deep)}
.foot-links{left:0;width:1038px;top:12px;text-align:center;color:#d8eef0;font-size:13px}
.foot-copy{left:0;width:1038px;top:42px;text-align:center;color:#d8eef0;font-size:12.5px}
.connect{right:10px;top:12px;color:#d8eef0;font-size:12.5px}
.social{right:10px;top:34px;display:flex;gap:8px}
.social span{width:24px;height:24px;background:#3f8f93;border:1px solid #8cc8cb}
</style>
</head>
<body>

<header>
  <div class="abs brand">
    <div class="brand-row"><span class="brand-mark">KVT</span><span class="brand-name">Torvello &amp; Associates, LLC</span></div>
    <div class="brand-tag">Intellectual Property and Cyber Security</div>
  </div>
  <nav class="abs nav">
    <a href="#">Home</a><a href="#">About KVT</a><a href="#">Practice Areas</a><a href="#">Associates</a><a href="#">Contact us</a>
  </nav>
</header>

<section class="abs slider">
  <div class="abs slide-stage">
    <div class="abs slide-photo" role="img" aria-label="Silver laptop secured for data protection"></div>
  </div>
</section>
<h1 class="abs slide-title">Data Protection</h1>
<p class="abs slide-copy">It has survived not only five centuries, but also the leap into electronic typesetting, remaining essentially unchanged. It was popularised in the 1960s with the release of Presstype sheets containing Lorem Ipsum passages, and more recently with desktop publishing software like Folio LayoutPro including versions of Lorem Ipsum.</p>
<div class="abs btn-grey">read more</div>
<div class="abs arrow prev"><svg width="12" height="16" viewBox="0 0 12 16"><path d="M9 1 3 8l6 7" fill="none" stroke="#555" stroke-width="2"/></svg></div>
<div class="abs arrow next"><svg width="12" height="16" viewBox="0 0 12 16"><path d="M3 1l6 7-6 7" fill="none" stroke="#555" stroke-width="2"/></svg></div>

<main>
  <div class="abs content"></div>

  <article class="abs card" style="left:26px">
    <div class="card-head">Cyber Security</div>
    <p>It has survived not only five centuries, but also the leap into electronic typesetting, remaining essentially unchanged. It was popularised in the 1960s with the release of Presstype sheets containing Lorem Ipsum passages, and more recently with desktop publishing software like Folio LayoutPro including versions of Lorem Ipsum.</p>
    <span class="btn">Read more</span>
  </article>
  <article class="abs card" style="left:284px">
    <div class="card-head">General Background<br>Investigations</div>
    <p>It has survived not only five centuries, but also the leap into electronic typesetting, remaining essentially unchanged. It was popularised in the 1960s with the release of Presstype sheets containing Lorem Ipsum passages, and more recently with desktop publishing software like Folio LayoutPro including versions of Lorem Ipsum.</p>
    <span class="btn">Read more</span>
  </article>
  <article class="abs card" style="left:543px">
    <div class="card-head">Data Protection</div>
    <p>It has survived not only five centuries, but also the leap into electronic typesetting, remaining essentially unchanged. It was popularised in the 1960s with the release of Presstype sheets containing Lorem Ipsum passages, and more recently with desktop publishing software like Folio LayoutPro including versions of Lorem Ipsum.</p>
    <span class="btn">Read more</span>
  </article>
  <article class="abs card" style="left:801px">
    <div class="card-head">Physical Security Services</div>
    <p>It has survived not only five centuries, but also the leap into electronic typesetting, remaining essentially unchanged. It was popularised in the 1960s with the release of Presstype sheets containing Lorem Ipsum passages, and more recently with desktop publishing software like Folio LayoutPro including versions of Lorem Ipsum.</p>
    <span class="btn">Read more</span>
  </article>

  <section class="abs welcome">
    <h2>Welcome To Our Company</h2>
    <p class="lead">It was popularised in the 1960s with the release of Presstype sheets containing Lorem Ipsum passages, and more recently with desktop publishing software like Folio LayoutPro including versions of Lorem Ipsum.</p>
  </section>
  <div class="abs person"><div role="img" aria-label="Portrait of a smiling consultant at a desk"></div></div>
  <p class="abs welcome-strong">It was popularised in the 1960s with the release of Presstype sheets containing</p>
  <p class="abs welcome-more">It was popularised in the 1960s with the release of Presstype sheets containing Lorem Ipsum passages, and more recently with desktop publishing software</p>

  <div class="abs divider" style="left:493px"></div>
  <section class="abs projects">
    <h2>Latest Projetcs</h2>
    <div class="project"><div class="thumb" role="img" aria-label="Project image"></div><p>It has survived not only five centuries, but also the leap into electronic typesetting.</p></div>
    <div class="project"><div class="thumb" role="img" aria-label="Project image" style="background:linear-gradient(135deg,#d9c27a,#5c5a4c)"></div><p>It has survived not only five centuries, but also the leap into electronic typesetting.</p></div>
    <div class="project"><div class="thumb" role="img" aria-label="Project image" style="background:linear-gradient(135deg,#2a6fa8,#0c2440)"></div><p>It has survived not only five centuries, but also the leap into electronic typesetting.</p></div>
  </section>

  <div class="abs divider" style="left:805px"></div>
  <section class="abs news">
    <h2>Latest News</h2>
    <div class="news-item"><div class="news-date">29.12.2011 &nbsp;|&nbsp; Wed &nbsp;|&nbsp; December</div><p>It has survived not only five centuries, but also the leap into electronic <a href="#">more.</a></p></div>
    <div class="news-item"><div class="news-date">29.12.2011 &nbsp;|&nbsp; Wed &nbsp;|&nbsp; December</div><p>It has survived not only five centuries, but also the leap into electronic <a href="#">more.</a></p></div>
    <div class="news-item"><div class="news-date">29.12.2011 &nbsp;|&nbsp; Wed &nbsp;|&nbsp; December</div><p>It has survived not only five centuries, but also the leap into electronic <a href="#">more.</a></p></div>
  </section>
</main>

<footer class="abs footer">
  <div class="abs foot-links">Home &nbsp;|&nbsp; About KVT &nbsp;|&nbsp; Practice Areas &nbsp;|&nbsp; Associates &nbsp;|&nbsp; Contact us</div>
  <div class="abs foot-copy">All 2011 &copy; &nbsp;copyrights. KVT Torvello &amp; Associates, LLC. received</div>
  <div class="abs connect">Connect with Us:</div>
  <div class="abs social" aria-label="Social links"><span></span><span></span><span></span><span></span><span></span></div>
</footer>

</body>
</html>
```